Industry / Entity Type

Financial consultancy / advisers

Current site is: http://www.brightmoor-counsel.com

Looking for a complete overhaul of this site, we are after a clean modern look. Will require the ability to easily add, update and remove content, hence the WordPress design.
Example:
Add case studies
Industry documentation (downloadable brochures / flyers and such)

What we like from our current site is the colour the fonts and the logo (the city of London) we would like to have other city outlines (NYC and Tokyo, Hong Kong, Singapore).

The site will be used by our potential clients to get in contact and re-view the case studies, if possible would like to have a client login area where they can download our documents like NDA’s etc and T&C’s.

Task Outline

Create a Web Design (Coded - Design and coding required)
Designer must provide full implementation/coding depending on the platform chosen by the client (i.e. WordPress theme, HTML/CSS, bootstrap etc.)

Task Description

I need a full website built that must work on desktop and mobile. I can provide the London city skyline and the font file, which we have used. Some stock industrial photos will be required.

Requirements:

*Splash page
*What We Do
*How We do it
*Who Are We? To have the same information and links as the current site
*Why use us?
*Clients: To have the same information and links as the current site
*Partners: To have the same information and links as the current site
*Contact:

Target Market(s)

Financial institutions trading Equities, Futures, Options, Forex and Fixed Income.
Regulators, Exchanges, ECN’s
Buy side firms and Sell side firms

Industry/Entity Type

Financial

Coding

Coded - Design and coding required

Number of Pages Required

5+ page

Font styles to use
Sans Serif

Colors
f04a50

Requirements
Must have
• Splash page
• What We Do
• How We do it
• Who Are We? To have the same information and links as the current site
• Why use us?
• Clients: To have the same information and links as the current site
• Partners: To have the same information and links as the current site
• Contact:

```html
<!DOCTYPE html>
<html lang="en">
<head>
<meta charset="utf-8">
<title>Brightmoor Counsel</title>
<link href="https://fonts.googleapis.com/css2?family=Carlito:wght@400;700&family=Cinzel:wght@700&family=Michroma&display=swap" rel="stylesheet">
<style>
:root{
  --brand:#f04a50;
  --ink:#333333;
  --muted:#777777;
  --soft:#f6f6f6;
  --white:#ffffff;
  --line:rgba(255,255,255,.25);
}
*{box-sizing:border-box;margin:0;padding:0}
html,body{width:668px;height:1200px;overflow:hidden;background:var(--white)}
body{font-family:"Carlito",Arial,sans-serif;color:var(--ink);position:relative}
.heading{font-family:"Cinzel",Georgia,serif;font-weight:700}

.site-header{position:absolute;top:0;left:0;width:668px;height:58px;background:var(--white)}
.brand{position:absolute;left:56px;top:20px;display:flex;align-items:center;gap:6px;font-family:"Carlito",sans-serif;font-weight:700;font-size:12px;letter-spacing:1.5px;color:var(--ink)}
.brand-mark{width:8px;height:8px;background:var(--brand)}
.main-nav{position:absolute;left:245px;top:30px;display:flex;gap:11px;font-family:"Cinzel",serif;font-weight:700;font-size:6.2px;letter-spacing:.2px}
.main-nav a{color:var(--ink);text-decoration:none}
.main-nav a.active{color:var(--brand);border-bottom:1px solid var(--brand);padding-bottom:5px}

.hero{position:absolute;top:58px;left:0;width:668px;height:330px;overflow:hidden}
.hero-photo{position:absolute;inset:0;background:linear-gradient(160deg,#5b5a4c 0%,#a39880 35%,#c8b79b 55%,#8c7a62 100%)}
.hero-title{position:absolute;top:108px;width:100%;text-align:center;font-family:"Michroma",sans-serif;font-size:19px;letter-spacing:4px;color:var(--white);text-transform:uppercase}
.hero-dots{position:absolute;top:267px;left:313px;display:flex;gap:3px}
.hero-dots span{width:9px;height:9px;border-radius:50%;background:var(--white)}
.hero-dots span.off{background:transparent;border:1.5px solid var(--white)}
.hero-curve{position:absolute;left:0;bottom:0}

.welcome{position:absolute;top:410px;left:0;width:668px;text-align:center}
.welcome h1{font-size:17px;letter-spacing:.5px;color:var(--ink)}
.welcome p{margin:14px auto 0;width:520px;font-size:6.6px;line-height:11px;color:var(--muted)}

.services{position:absolute;top:500px;left:56px;width:560px;display:grid;grid-template-columns:196px 192px 172px;row-gap:50px}
.service{display:flex;gap:8px}
.service svg{flex:none}
.service h3{font-family:"Cinzel",serif;font-weight:700;font-size:9.5px;letter-spacing:.4px;color:var(--ink);margin-top:5px}
.service p{margin-top:8px;font-size:7.2px;line-height:13px;color:var(--muted);width:130px}

.about{position:absolute;top:692px;left:0;width:668px;height:294px;background:var(--soft)}
.about h2{position:absolute;left:56px;top:36px;font-size:18px;color:var(--brand)}
.about .lead{position:absolute;left:56px;top:66px;width:300px;font-size:9.5px;line-height:14px;color:var(--ink)}
.about .body{position:absolute;left:56px;top:104px;width:275px;font-size:6.6px;line-height:14px;color:var(--muted)}
.about .body p+p{margin-top:3px}
.btn{position:absolute;left:56px;top:224px;width:82px;height:26px;background:var(--brand);color:var(--white);font-family:"Cinzel",serif;font-weight:700;font-size:9.5px;display:flex;align-items:center;justify-content:center;border-radius:2px}
.about-photo{position:absolute;left:372px;top:40px;width:242px;height:203px;border:3px solid var(--white);border-radius:3px;background:linear-gradient(120deg,#dfe3e6 0%,#b9c0c6 40%,#3c4a5c 70%,#c9b79f 100%);box-shadow:0 0 4px rgba(0,0,0,.1)}

.site-footer{position:absolute;top:986px;left:0;width:668px;height:166px;background:var(--brand);color:var(--white)}
.footer-col{position:absolute;top:24px}
.footer-col h4{font-family:"Cinzel",serif;font-weight:700;font-size:12.5px;letter-spacing:.3px}
.divider{position:absolute;top:24px;width:1px;height:114px;background:var(--line)}
.quick-links{left:56px;width:170px}
.quick-links ul{list-style:none;margin-top:14px;display:grid;grid-template-columns:100px 70px;row-gap:4.5px;font-size:8px}
.contact{left:266px;width:145px}
.contact address{font-style:normal;margin-top:10px;font-size:8px;line-height:14.5px}
.contact .row{display:flex;align-items:center;gap:6px;font-size:8px;margin-top:4px}
.contact .row:first-of-type{margin-top:8px}
.newsletter{left:440px;width:174px}
.signup{margin-top:9px;width:174px;height:24px;background:var(--white);border-radius:2px;position:relative}
.signup span{position:absolute;left:8px;top:8px;font-size:6.8px;color:#999;letter-spacing:.3px}
.signup b{position:absolute;right:5px;top:4px;height:16px;padding:0 5px;background:var(--brand);color:var(--white);font-size:6.8px;line-height:16px;border-radius:2px;letter-spacing:.3px}
.social{display:flex;gap:5px;margin-top:10px}
.social span{width:20px;height:20px;border-radius:50%;background:var(--white)}

.legal{position:absolute;top:1152px;left:0;width:668px;height:48px;text-align:center;font-size:6.6px;line-height:48px;color:var(--ink)}
</style>
</head>
<body>
<header class="site-header">
  <div class="brand"><span class="brand-mark"></span>BRIGHTMOOR COUNSEL</div>
  <nav class="main-nav">
    <a class="active" href="#">HOME</a><a href="#">WHAT WE DO</a><a href="#">HOW WE DO IT</a><a href="#">WHO ARE WE</a><a href="#">WHY USE US</a><a href="#">CLIENTS</a><a href="#">PARTNERS</a><a href="#">CONTACT</a>
  </nav>
</header>

<section class="hero">
  <div class="hero-photo" role="img" aria-label="Upward view of tall city office towers and a columned building under a pale sky"></div>
  <h2 class="hero-title">Financial Consulting Firm</h2>
  <div class="hero-dots"><span class="off"></span><span></span><span></span><span></span></div>
  <svg class="hero-curve" width="668" height="40" viewBox="0 0 668 40"><path d="M0 40 L0 22 Q334 -18 668 22 L668 40 Z" fill="#ffffff"/></svg>
</section>

<section class="welcome">
  <h1 class="heading">WELCOME TO BRIGHTMOOR COUNSEL</h1>
  <p>Since founding Brightmoor Counsel in 2014 we have dedicated ourselves to the provision of services. What differentiates us from other advisers or consultancies is a genuine motivation to see our clients succeed. Today's technology allows our clients to take their knowledge to the market in ways that previous generations could only dream of. That's why BMC is dedicated to seeing you choose the right technology strategy, ensuring you maintain a competitive edge over your peers.</p>
</section>

<section class="services">
  <div class="service">
    <svg width="30" height="30" viewBox="0 0 30 30" fill="#f04a50"><circle cx="6" cy="5" r="3"/><rect x="3" y="9" width="6" height="11" rx="1"/><rect x="3.5" y="19" width="2" height="9"/><rect x="6.5" y="19" width="2" height="9"/><rect x="12" y="3" width="16" height="12" fill="none" stroke="#f04a50" stroke-width="1.5"/><path d="M8 11 L14 8" stroke="#f04a50" stroke-width="1.5"/></svg>
    <div><h3>Training</h3><p>Trading Technology for Compliance and non technical staff.</p></div>
  </div>
  <div class="service">
    <svg width="30" height="30" viewBox="0 0 30 30" fill="#f04a50"><ellipse cx="14" cy="18" rx="11" ry="8"/><rect x="8" y="23" width="3" height="5"/><rect x="17" y="23" width="3" height="5"/><circle cx="21" cy="6" r="5"/></svg>
    <div><h3>Advice</h3><p>Board Level advisory &amp; Programe Management.</p></div>
  </div>
  <div class="service">
    <svg width="32" height="30" viewBox="0 0 32 30" fill="none" stroke="#f04a50" stroke-width="1.5"><rect x="3" y="4" width="26" height="17" rx="1"/><path d="M1 24 H31"/><path d="M7 15 L12 9 L16 13 L20 8 L25 14"/></svg>
    <div><h3>Product Development</h3><p>Front-Office Trading platforms and Market Data.</p></div>
  </div>
  <div class="service">
    <svg width="30" height="30" viewBox="0 0 30 30" fill="#f04a50"><path d="M2 10 L15 3 L28 10 V28 H2 Z"/><rect x="7" y="14" width="16" height="2" fill="#fff"/><rect x="7" y="19" width="16" height="2" fill="#fff"/><rect x="7" y="24" width="16" height="2" fill="#fff"/></svg>
    <div><h3>Interim Management</h3><p>For Funds, Broker, Vendors and IT Service Providers.</p></div>
  </div>
  <div class="service">
    <svg width="30" height="30" viewBox="0 0 30 30" fill="#f04a50"><circle cx="12" cy="18" r="9"/><circle cx="12" cy="18" r="3.5" fill="#fff"/><circle cx="23" cy="6" r="4.5"/><circle cx="23" cy="6" r="1.8" fill="#fff"/></svg>
    <div><h3>Process Outsourcing</h3><p>RFI, RFP &amp; Independent tender evaluations (assess before you invest)</p></div>
  </div>
  <div class="service">
    <svg width="30" height="30" viewBox="0 0 30 30" fill="#f04a50"><circle cx="15" cy="14" r="7"/><rect x="12" y="20" width="6" height="6" rx="1"/><path d="M15 1 V4 M4 14 H1 M29 14 H26 M6 5 L8 7 M24 5 L22 7" stroke="#f04a50" stroke-width="1.5"/></svg>
    <div><h3>Research</h3><p>Topical Paper White labelled and sponsered articles.</p></div>
  </div>
</section>

<section class="about">
  <h2 class="heading">About Us</h2>
  <p class="lead">Since founding Brightmoor Counsel in 2014 we have dedicated ourselves to the provision of services</p>
  <div class="body">
    <p>Since founding Brightmoor Counsel in 2014 we have dedicated ourselves to the provision of services. What differentiates us from other advisers or consultancies is a genuine motivation to see our clients succeed. Today's technology allows our clients to take their knowledge to the market in ways that previous generations could only dream of.</p>
    <p>BMC is dedicated to seeing you choose the right technology strategy, ensuring you maintain a competitive edge over your peers.</p>
  </div>
  <a class="btn" href="#">Read More »</a>
  <div class="about-photo" role="img" aria-label="Two business advisers reviewing documents and a tablet at a bright office desk"></div>
</section>

<footer class="site-footer">
  <div class="footer-col quick-links">
    <h4>Quick Links</h4>
    <ul><li>Home</li><li>Why use us</li><li>What we do</li><li>Clients</li><li>How we do it</li><li>Partners</li><li>Who are we</li><li>Contact</li></ul>
  </div>
  <span class="divider" style="left:235px"></span>
  <div class="footer-col contact">
    <h4>Contact Us</h4>
    <address>Suite 4 Harlow Court, Fenbridge,<br>Northam, Kent, NK7 2RB</address>
    <div class="row"><svg width="9" height="9" viewBox="0 0 10 10" fill="#fff"><path d="M2 0 L4 2.5 L3 4 Q4.5 6 6 7 L7.5 6 L10 8 L8.5 10 Q3 9 0 2 Z"/></svg>+11 01 07315582</div>
    <div class="row"><svg width="10" height="8" viewBox="0 0 10 8" fill="#fff"><rect width="10" height="8" rx="1"/><path d="M0.5 1 L5 4.5 L9.5 1" stroke="#f04a50" fill="none"/></svg>admin@brightmoor-counsel.com</div>
  </div>
  <span class="divider" style="left:417px"></span>
  <div class="footer-col newsletter">
    <h4>Join Newsletters</h4>
    <div class="signup"><span>EMAIL ADDRESS</span><b>SUBSCRIBE</b></div>
    <div class="social"><span></span><span></span><span></span><span></span><span></span></div>
  </div>
</footer>

<div class="legal">© 2017 Brightmoor Counsel. All right reserved. Term of Use</div>
</body>
</html>
```